I need to make a car magnet

It needs to include the words "PLAVO TOUR" and "2026 MEMBER" as well as the attached silhouette of the golfer. The color scheme needs to be navy, red and white. The shape and dimensions are open for interpretation

```html
<!DOCTYPE html>
<html lang="en">
<head>
<meta charset="UTF-8">
<title>Plavo Tour 2026 Member – Car Magnet</title>
<link rel="stylesheet" href="https://fonts.googleapis.com/css2?family=Bitter:wght@800&family=Montserrat:wght@500;700&display=swap">
<style>
  :root {
    --stage-grey: #b8b8b8;
    --spec-teal: #1f6384;
    --navy: #24386f;
    --red: #cc2a2b;
    --red-on-navy: #7c3152;
    --red-tint: #f4cccc;
    --white: #ffffff;
  }
  * { margin: 0; padding: 0; box-sizing: border-box; }
  html, body {
    width: 1200px;
    height: 1000px;
    overflow: hidden;
    background: var(--stage-grey);
  }
  .canvas {
    position: relative;
    width: 1200px;
    height: 1000px;
  }
  .size-spec {
    position: absolute;
    top: 30px;
    left: 0;
    width: 1172px;
    text-align: center;
    font-family: "Montserrat", sans-serif;
    font-weight: 500;
    font-size: 53px;
    letter-spacing: 0.5px;
    color: var(--spec-teal);
  }
  .magnet {
    position: absolute;
    width: 426px;
    height: 639px;
  }
  .magnet--navy { left: 130px; top: 178px; background: var(--navy); }
  .magnet--white { left: 631px; top: 179px; background: var(--white); }
  .magnet svg { display: block; width: 100%; height: 100%; }
  .magnet--navy .golfer-art { fill: var(--red-on-navy); }
  .magnet--white .golfer-art { fill: var(--red-tint); }
  .title {
    font-family: "Bitter", serif;
    font-weight: 800;
    font-size: 78px;
    letter-spacing: 4px;
  }
  .year {
    font-family: "Montserrat", sans-serif;
    font-weight: 700;
    font-size: 108px;
  }
  .member {
    font-family: "Montserrat", sans-serif;
    font-weight: 700;
    font-size: 29px;
  }
  .magnet--navy .ink { fill: var(--white); }
  .magnet--white .ink { fill: var(--navy); }
</style>
</head>
<body>
<main class="canvas">
  <h1 class="size-spec">Width- 12 inch, Height- 18 inch</h1>

  <section class="magnet magnet--navy">
    <svg viewBox="0 0 426 639" xmlns="http://www.w3.org/2000/svg">
      <rect class="golfer-art" x="48" y="70" width="330" height="512" rx="40"
            role="img" aria-label="Red silhouette of a golfer putting a ball"/>
      <text class="title ink" x="215" y="264" text-anchor="middle">PLAVO</text>
      <text class="title ink" x="215" y="370" text-anchor="middle">TOUR</text>
      <text class="year ink" x="215" y="500" text-anchor="middle">2026</text>
      <text class="member ink" x="213" y="544" text-anchor="middle">MEMBER</text>
    </svg>
  </section>

  <section class="magnet magnet--white">
    <svg viewBox="0 0 426 639" xmlns="http://www.w3.org/2000/svg">
      <rect class="golfer-art" x="48" y="70" width="330" height="512" rx="40"
            role="img" aria-label="Red silhouette of a golfer putting a ball"/>
      <text class="title ink" x="215" y="263" text-anchor="middle">PLAVO</text>
      <text class="title ink" x="215" y="369" text-anchor="middle">TOUR</text>
      <text class="year ink" x="215" y="499" text-anchor="middle">2026</text>
      <text class="member ink" x="213" y="543" text-anchor="middle">MEMBER</text>
    </svg>
  </section>
</main>
</body>
</html>
```